Silas Merton Moving DL Flyer

We need a double sided DL flyer to give to patients to let them know that we are moving location.
On one side we would like it to read:
"We Are Moving!" and "November 2017" and our logo.
On the other side we would like it to read:
"Same Great Staff"
"Same Great Service"
"Bigger, Brighter and Better"
"New Location at 59 Quarry Ln"
with a map below (attached)
The flyer should follow our practice branding. Attached is a copy of our business card as an example of this.

```html
<!DOCTYPE html>
<html lang="en">
<head>
<meta charset="utf-8">
<title>Silas Merton Optometry – Moving Flyer</title>
<link rel="stylesheet" href="https://fonts.googleapis.com/css2?family=Roboto+Condensed:wght@700&family=Open+Sans:wght@400;600;700&display=swap">
<style>
  :root {
    --backdrop: #e7e4e9;
    --paper: #ffffff;
    --purple: #7b5b8c;
    --purple-light: #a687b3;
    --purple-dark: #4d3658;
    --ink: #3a2d40;
    --ink-soft: #555055;
    --photo-a: #c9d4de;
    --photo-b: #eef2f5;
    --map-grey: #c8c8c8;
  }
  * { box-sizing: border-box; margin: 0; padding: 0; }
  html, body { width: 1200px; height: 1020px; overflow: hidden; }
  body {
    background: var(--backdrop);
    font-family: "Open Sans", Arial, sans-serif;
    position: relative;
  }
  .flyer {
    position: absolute;
    top: 91px;
    width: 420px;
    height: 838px;
    background: var(--paper);
    box-shadow: 0 6px 18px rgba(0,0,0,.18);
    overflow: hidden;
  }
  .flyer--front { left: 170px; }
  .flyer--back { left: 610px; }

  .brand {
    position: absolute;
    top: 38px;
    left: 0;
    right: 0;
    display: flex;
    justify-content: center;
    align-items: center;
    gap: 12px;
  }
  .brand__mark {
    width: 22px; height: 22px;
    background: var(--ink);
  }
  .brand__name {
    font-family: "Open Sans", Arial, sans-serif;
    font-weight: 600;
    font-size: 27px;
    color: var(--ink);
    letter-spacing: -.3px;
  }

  .hero {
    position: absolute;
    top: 112px;
    left: 0;
    width: 420px;
    height: 450px;
  }

  .banner {
    position: absolute;
    left: 0; right: 0;
    top: 568px;
    height: 192px;
    border-top: 8px solid var(--purple);
    border-bottom: 8px solid var(--purple);
    padding: 10px 0;
  }
  .banner__fill {
    height: 100%;
    background: linear-gradient(90deg, var(--purple) 0%, var(--purple-light) 50%, var(--purple) 100%);
    border-top: 2px solid #fff;
    border-bottom: 2px solid #fff;
    display: flex;
    flex-direction: column;
    align-items: center;
    justify-content: center;
    color: #fff;
    font-family: "Roboto Condensed", "Arial Narrow", sans-serif;
    font-weight: 700;
  }
  .banner__title { font-size: 54px; line-height: 1; }
  .banner__date { font-size: 28px; margin-top: 8px; }
  .site-url {
    position: absolute;
    left: 0; right: 0;
    top: 783px;
    text-align: center;
    font-weight: 700;
    font-size: 20px;
    color: var(--ink);
  }

  .promise {
    position: absolute;
    left: 0; right: 0;
    top: 568px;
    text-align: center;
    color: var(--purple-dark);
    font-family: "Roboto Condensed", "Arial Narrow", sans-serif;
    font-weight: 700;
  }
  .promise__main { font-size: 44px; line-height: 1.05; }
  .promise__sub { font-size: 27px; margin-top: 4px; }
  .strapline {
    position: absolute;
    left: 0; right: 0;
    top: 657px;
    height: 72px;
    background: linear-gradient(90deg, var(--purple) 0%, var(--purple-light) 50%, var(--purple) 100%);
    color: #fff;
    font-family: "Roboto Condensed", "Arial Narrow", sans-serif;
    font-weight: 700;
    font-size: 29px;
    text-transform: uppercase;
    display: flex;
    align-items: center;
    justify-content: center;
  }
  .contact {
    position: absolute;
    left: 16px; right: 16px;
    top: 750px;
    height: 80px;
    display: flex;
    align-items: center;
  }
  .contact__call {
    width: 205px;
    color: var(--ink);
    font-family: "Roboto Condensed", "Arial Narrow", sans-serif;
    font-weight: 700;
  }
  .contact__label { font-size: 19px; }
  .contact__phone { font-size: 42px; line-height: 1; }
  .contact__list {
    list-style: none;
    border-left: 1px solid #b9b3bc;
    padding-left: 12px;
    font-size: 12.5px;
    color: var(--ink-soft);
  }
  .contact__list li {
    display: flex;
    align-items: center;
    gap: 8px;
    line-height: 22px;
  }
  .contact__list svg { flex: none; }
</style>
</head>
<body>

<section class="flyer flyer--front">
  <header class="brand">
    <span class="brand__mark"></span>
    <span class="brand__name">Silas Merton Optometry</span>
  </header>
  <svg class="hero" viewBox="0 0 420 450" aria-hidden="false">
    <defs>
      <linearGradient id="swoosh-front" x1="0" x2="1">
        <stop offset="0" stop-color="#7b5b8c"/>
        <stop offset=".5" stop-color="#a687b3"/>
        <stop offset="1" stop-color="#7b5b8c"/>
      </linearGradient>
      <linearGradient id="photo-tone" x1="0" y1="0" x2="1" y2="1">
        <stop offset="0" stop-color="#dfe6ec"/>
        <stop offset=".55" stop-color="#b9c5d0"/>
        <stop offset="1" stop-color="#eef2f5"/>
      </linearGradient>
    </defs>
    <path d="M0,48 Q210,-18 420,52 L420,86 Q210,10 0,78 Z" fill="url(#swoosh-front)"/>
    <path role="img" aria-label="Photo of an optometrist examining a patient's eyes with a slit lamp"
          d="M0,84 Q210,16 420,92 L420,370 Q210,440 0,352 Z" fill="url(#photo-tone)"/>
    <path d="M0,360 Q210,448 420,378 L420,412 Q210,470 0,392 Z" fill="url(#swoosh-front)"/>
  </svg>
  <div class="banner">
    <div class="banner__fill">
      <span class="banner__title">We Are Moving</span>
      <span class="banner__date">November 2017</span>
    </div>
  </div>
  <p class="site-url">www.silasmerton.com.au</p>
</section>

<section class="flyer flyer--back">
  <header class="brand">
    <span class="brand__mark"></span>
    <span class="brand__name">Silas Merton Optometry</span>
  </header>
  <svg class="hero" viewBox="0 0 420 450">
    <defs>
      <linearGradient id="swoosh-back" x1="0" x2="1">
        <stop offset="0" stop-color="#7b5b8c"/>
        <stop offset=".5" stop-color="#a687b3"/>
        <stop offset="1" stop-color="#7b5b8c"/>
      </linearGradient>
    </defs>
    <path d="M0,48 Q210,-18 420,52 L420,86 Q210,10 0,78 Z" fill="url(#swoosh-back)"/>
    <path role="img" aria-label="Street map showing the new practice location near the marketplace"
          d="M0,84 Q210,16 420,92 L420,370 Q210,440 0,352 Z" fill="#c8c8c8"/>
    <path d="M0,360 Q210,448 420,378 L420,412 Q210,470 0,392 Z" fill="url(#swoosh-back)"/>
  </svg>
  <div class="promise">
    <p class="promise__main">Same Great Staff</p>
    <p class="promise__sub">Same Great Service</p>
  </div>
  <div class="strapline">Bigger, Brighter and Better</div>
  <div class="contact">
    <div class="contact__call">
      <p class="contact__label">CALL NOW</p>
      <p class="contact__phone">6550 2184</p>
    </div>
    <ul class="contact__list">
      <li>
        <svg width="11" height="11" viewBox="0 0 12 12"><circle cx="6" cy="6" r="5.5" fill="none" stroke="#555055"/><path d="M6,2.5a2,2 0 0 1 2,2c0,1.5-2,4-2,4s-2-2.5-2-4a2,2 0 0 1 2-2z" fill="#555055"/></svg>
        New Location at 59 Quarry Ln
      </li>
      <li>
        <svg width="11" height="11" viewBox="0 0 12 12"><circle cx="6" cy="6" r="5.5" fill="none" stroke="#555055"/><rect x="3" y="4" width="6" height="4" fill="#555055"/></svg>
        silas@silasmerton.com.au
      </li>
      <li>
        <svg width="11" height="11" viewBox="0 0 12 12"><circle cx="6" cy="6" r="5.5" fill="none" stroke="#555055"/><circle cx="6" cy="6" r="2.6" fill="none" stroke="#555055"/></svg>
        www.silasmerton.com.au
      </li>
    </ul>
  </div>
</section>

</body>
</html>
```